New Cryotherapy Business needs a Flyer Design

We are expanding our massage business located in Sydney with a Cryosauna. We need a flyer/brochure that explain what whole body cryotherapy is and all its benefits in a very simple way as we are the first cryotherapy business in Sydney and not many people knows what it is yet. We would like to see a design that use the color of our logo or shades of blue that comunicate freshness, innovation and health but also movement and sport performance. The flyer targets gym's members, athletes and also yoga/pilates goers with a focus on wellbeing and health.

Please find attached our logo (we actually prefer to use the logo/font in the banner adding the hand underneath the vitruvian man) and some examples of cryotherapy flyers with the information about the product/service we would like to include in the flyer. We would like also to include a section with special offer for new clients.

Target Market(s)

The flyer targets gym's members, athletes and also yoga/pilates goers with a focus on wellbeing and health.

Industry/Entity Type

Health And Wellness

Font styles to use
Sans Serif

Colors
f78f20
848484
c3c3c3
85acd3
0792cd
3176b5

Requirements
Must have
• logo, contact details, FAQs, About WBC, Benefits, Applications include, special offer for new clients section, pic of cryosauna with muscular guy, logos of "as seen on tv"

```html
<!DOCTYPE html>
<html lang="en">
<head>
<meta charset="utf-8">
<title>Whole Body Cryotherapy Flyer</title>
<link rel="stylesheet" href="https://fonts.googleapis.com/css2?family=Open+Sans:wdth,wght@75..100,400..800&family=Arimo:wght@400&display=swap">
<style>
  :root{
    --orange:#f78f20;
    --orange-soft:#fdc35a;
    --grey:#848484;
    --grey-light:#c3c3c3;
    --sky:#85acd3;
    --cyan:#0792cd;
    --blue:#3176b5;
    --navy:#101722;
    --box-blue:rgba(133,172,211,.82);
    --white:#ffffff;
  }
  *{margin:0;padding:0;box-sizing:border-box}
  html,body{width:1200px;height:848px;overflow:hidden;background:var(--navy)}
  .flyer{
    position:relative;width:1200px;height:848px;overflow:hidden;
    background:
      radial-gradient(ellipse 520px 300px at 380px 760px, rgba(90,130,170,.35), transparent 70%),
      radial-gradient(ellipse 420px 420px at 1150px 520px, rgba(90,130,170,.35), transparent 70%),
      linear-gradient(160deg,#0c121b 0%,#1b2a3b 45%,#2c4158 75%,#1a2636 100%);
  }
  .edge{position:absolute;left:0;top:0;width:10px;height:848px;background:#3a4b5e}
  .swimmer-photo{
    position:absolute;left:10px;top:0;width:560px;height:421px;
    background:
      radial-gradient(ellipse 260px 120px at 270px 210px, rgba(200,210,220,.45), transparent 70%),
      radial-gradient(ellipse 80px 50px at 275px 215px, rgba(170,110,80,.55), transparent 70%),
      linear-gradient(180deg,#06090d 0%,#141c24 55%,#2a3540 100%);
    -webkit-mask-image:linear-gradient(180deg,#000 75%,transparent 100%);
    mask-image:linear-gradient(180deg,#000 75%,transparent 100%);
  }
  .cond{font-family:"Open Sans",sans-serif;font-stretch:75%;font-weight:700}
  .left-title{
    position:absolute;left:10px;top:284px;width:552px;text-align:center;
    font-family:"Open Sans",sans-serif;font-weight:700;color:var(--white);
    font-size:50px;line-height:46px;letter-spacing:-.5px;
  }
  .left-title .sub{display:block;font-weight:600;font-size:32px;line-height:40px;margin-top:2px}
  .cryo{color:var(--sky)}
  .therapy{color:var(--orange)}
  .about{
    position:absolute;left:23px;top:421px;width:557px;height:186px;
    background:var(--box-blue);padding:7px 0 0;
    color:var(--white);font-size:14px;line-height:25.3px;text-align:center;
    text-transform:uppercase;white-space:nowrap;
  }
  .about-extend{position:absolute;left:580px;top:421px;width:133px;height:186px;background:rgba(133,172,211,.35)}
  .applications{
    position:absolute;left:178px;top:607px;width:240px;height:232px;
    background:var(--orange);padding:6px 13px;
    font-family:"Arimo",sans-serif;color:var(--white);
  }
  .applications h3{font-weight:400;font-size:14px;color:var(--orange-soft);margin-bottom:18px;letter-spacing:.2px}
  .applications ul{list-style:none;font-size:13px;line-height:15.2px}
  .applications li{padding-left:9px;text-indent:-9px}
  .applications li::before{content:"• "}
  .rule{position:absolute;width:1px;background:rgba(255,255,255,.75)}
  .panel-svg{position:absolute;left:0;top:0}
  .neck-photo{
    position:absolute;left:812px;top:0;width:388px;height:305px;
    background:
      radial-gradient(ellipse 70px 80px at 200px 45px, #1a1a1a, transparent 72%),
      radial-gradient(ellipse 70px 90px at 150px 190px, rgba(247,143,32,.75), transparent 70%),
      radial-gradient(ellipse 80px 90px at 250px 190px, rgba(49,118,181,.75), transparent 70%),
      radial-gradient(ellipse 170px 140px at 200px 230px, #bdbdbd, transparent 75%);
  }
  .right-title{
    position:absolute;left:609px;top:82px;
    font-family:"Open Sans",sans-serif;font-weight:700;color:var(--orange);
    font-size:50px;line-height:46px;letter-spacing:-.5px;
  }
  .right-title .sub{display:block;font-weight:600;font-size:32px;line-height:40px;margin-top:2px;margin-left:1px}
  .title-rule{position:absolute;left:598px;top:213px;width:225px;height:1px;background:var(--orange)}
  .brand{
    position:absolute;left:613px;top:226px;width:130px;height:49px;background:var(--white);
    display:flex;align-items:center;justify-content:center;gap:7px;
  }
  .brand-dot{width:14px;height:14px;border-radius:50%;background:var(--blue)}
  .brand-name{font-family:"Open Sans",sans-serif;font-weight:700;font-size:15px;color:var(--blue);letter-spacing:.5px}
  .offer-column{
    position:absolute;left:717px;top:322px;width:367px;height:526px;
    background:linear-gradient(180deg,#7d7f82 0%,#66696d 40%,#5a5d62 100%);
  }
  .column-line{position:absolute;top:322px;width:3px;height:526px;background:var(--sky)}
  .offer{
    position:absolute;left:717px;top:380px;width:367px;text-align:center;
    font-size:13px;color:var(--white);
  }
  .offer .hl{color:var(--orange)}
  .how-title{
    position:absolute;left:717px;top:414px;width:367px;text-align:center;
    font-family:"Open Sans",sans-serif;font-weight:700;font-size:24px;color:var(--white);
    display:flex;align-items:center;justify-content:center;gap:8px;
  }
  .how-box{
    position:absolute;left:719px;top:458px;width:363px;height:135px;
    background:var(--box-blue);padding:4px 0 0 9px;
    font-size:11.5px;line-height:22.4px;white-space:nowrap;
    color:var(--white);text-transform:uppercase;
  }
  .sauna-photo{
    position:absolute;left:830px;top:593px;width:148px;height:246px;
    background:
      radial-gradient(ellipse 40px 70px at 95px 130px, rgba(200,160,130,.7), transparent 72%),
      radial-gradient(ellipse 60px 110px at 100px 170px, rgba(230,230,235,.55), transparent 75%),
      linear-gradient(90deg,#2b2c2f 0%,#3d3e42 45%,#9a9ca0 70%,#3a3b3f 100%);
  }
  .caption{
    position:absolute;left:729px;top:810px;width:144px;height:29px;
    background:var(--box-blue);padding:2px 0 0 7px;
    font-size:10px;line-height:12.5px;white-space:nowrap;
    color:var(--white);text-transform:uppercase;
  }
</style>
</head>
<body>
<main class="flyer">
  <div class="edge"></div>

  <div class="swimmer-photo" role="img" aria-label="Photo of a swimmer doing butterfly stroke with water splashing"></div>

  <h1 class="left-title">WHOLE<br>BODY<span class="sub"><span class="cryo">CRYO</span><span class="therapy">THERAPY</span></span></h1>

  <div class="about-extend"></div>
  <p class="about cond">Professional athletes have discovered WBC as a powerful treatment to de-<br>crease recovery time and increase athletic performance. Although whole<br>body cryotherapy originated in Japan, it was a group of Polish scientists<br>who took the idea and made whole body cryotherapy the physical therapy<br>it is today. The Northfield Athletic Recovery Center in Lakeview opened in May<br>2000 and has been used as a training and injury rehabilitation center for<br>many athletes.</p>

  <section class="applications">
    <h3>APPLICATIONS</h3>
    <ul>
      <li>Athletic performance</li>
      <li>Postsurgical recovery</li>
      <li>Rheumatoid Arthritis</li>
      <li>Burn up to 800 calories</li>
      <li>Increased metabolism</li>
      <li>Sleep better</li>
      <li>Better mood</li>
      <li>Increased energy</li>
      <li>Autoimmune disorders</li>
      <li>Skin conditions such as dermatitis and psoriasis</li>
      <li>Improved skin elasticity</li>
    </ul>
  </section>

  <div class="rule" style="left:580px;top:379px;height:276px"></div>
  <div class="rule" style="left:600px;top:379px;height:469px"></div>

  <svg class="panel-svg" width="1200" height="420" viewBox="0 0 1200 420" aria-hidden="true">
    <defs>
      <linearGradient id="panelFill" x1="0" y1="0" x2="1" y2="1">
        <stop offset="0" stop-color="#8a8c8f"/>
        <stop offset=".35" stop-color="#e6e6e6"/>
        <stop offset="1" stop-color="#f2f2f2"/>
      </linearGradient>
    </defs>
    <path d="M340 40 L566 37 L566 62 L340 64 Z" fill="#2f5f95" opacity=".7"/>
    <path d="M550 0 C570 120 560 260 538 392 C600 340 700 300 860 302 C1000 304 1100 320 1200 300 L1200 330 C1100 345 1000 330 860 330 C720 330 620 360 552 420 Z" fill="#4b4e53"/>
    <path d="M562 0 L1200 0 L1200 300 C1100 320 1000 304 860 302 C700 300 600 340 544 387 C566 260 576 120 562 0 Z" fill="url(#panelFill)"/>
    <path d="M566 37 C800 25 1000 10 1200 0 L1200 16 C1000 30 800 48 566 61 Z" fill="#85acd3" opacity=".9"/>
  </svg>

  <div class="neck-photo" role="img" aria-label="Photo of a woman seen from behind holding her neck, one shoulder tinted orange and one blue"></div>

  <h2 class="right-title">WHOLE<br>BODY<span class="sub"><span class="cryo">CRYO</span><span class="therapy">THERAPY</span></span></h2>
  <div class="title-rule"></div>
  <div class="brand"><span class="brand-dot"></span><span class="brand-name">KELVA</span></div>

  <div class="offer-column"></div>
  <div class="column-line" style="left:713px"></div>
  <div class="column-line" style="left:1082px"></div>

  <p class="offer cond"><span class="hl">SPECIAL</span> OFFER FOR NEW CLIENTS</p>
  <h3 class="how-title">
    <svg width="20" height="18" viewBox="0 0 20 18" aria-hidden="true"><path d="M2 9 L8 15 L18 2" fill="none" stroke="#fff" stroke-width="3.5" stroke-linecap="round" stroke-linejoin="round"/></svg>
    HOW IT WORKS:
  </h3>
  <p class="how-box cond">With whole body cryotherapy (WBC) the body is exposed to ul-<br>tra-low temperatures (-200 to -240 F).<br>&nbsp;The client is placed in a cryogenic sauna/chamber for a short du-<br>ration of 1.5-3 minutes which lowers the client's skin surface te-<br>perature significantly and stimulates receptors</p>

  <div class="sauna-photo" role="img" aria-label="Photo of a muscular man stepping out of an open cryosauna cabin with cold vapour"></div>
  <p class="caption cond">Clients are protected with<br>socks, gloves, and slippers</p>
</main>
</body>
</html>
```